Sell the dream! Property investment proposal document

We are looking for a proposal document which outlines our vision for property development. The purpose of the document is to raise investment from investors - sell the dream!
Brief summary:
Kestrel Dwellings Developments, is an emerging New Zealand property investment company with a focus on providing unique property investment opportunities.
Our expertise and capabilities in architectural modular homes provide us with a remarkable advantage in tackling the development of properties that are typically considered challenging, remote, or uniquely positioned.
Our specialization in this niche sector of property development not only sets us apart from competitors, but also paves the way for lucrative investment opportunities in the New Zealand property market.
Feel free to use any images from www.kestreldwellings.co.nz
Target Market(s)
investors for a unique property development opportunity
Industry/Entity Type
luxury property development in unique locations throughout New Zealand
Colors
Designer to choose only greyscale colors for use in the design.
Look and feel

```html
<!DOCTYPE html>
<html lang="en">
<head>
<meta charset="utf-8">
<title>Kestrel Dwellings – Property Investment Proposal</title>
<link rel="stylesheet" href="https://fonts.googleapis.com/css2?family=Jost:wght@300;400&family=Gilda+Display&family=Poppins:wght@300;400&display=swap">
<style>
  :root{
    --paper:#ffffff;
    --ink-dark:#1c1c1c;
    --ink-body:#3a3a3a;
    --panel:#1e1e1e;
    --white:#ffffff;
    --soft-white:#e6e6e6;
    --rule:#8a8a8a;
  }
  *{margin:0;padding:0;box-sizing:border-box}
  html,body{width:1200px;height:936px;overflow:hidden;background:var(--paper)}
  body{position:relative;font-family:"Poppins",sans-serif;font-weight:300}
  .sheet-frame{position:absolute;inset:0;border:1px solid #bdbdbd}
  .page{position:absolute;width:274px;height:388px;overflow:hidden;background:var(--panel)}
  .photo{position:absolute;left:0;right:0;top:0}
  .panel{position:absolute;left:0;right:0;bottom:0;background:var(--panel)}
  .heading{position:absolute;left:19px;font-family:"Gilda Display",serif;line-height:.9;color:var(--white)}
  .heading .small{display:block;font-size:16px}
  .heading .large{display:block;font-size:31px}
  .copy{position:absolute;font-size:4.4px;line-height:1.65;color:var(--soft-white)}
  .copy p{margin-bottom:4.6px}
  .copy u{text-decoration:underline}
  .page-footer{position:absolute;left:17px;right:17px;bottom:14px;height:14px;display:flex;align-items:center;gap:8px}
  .wordmark{font-family:"Jost",sans-serif;font-weight:400;font-size:10px;color:var(--white);letter-spacing:.2px}
  .footer-rule{flex:1;height:0;border-top:.6px solid var(--rule)}
  .folio{width:15px;height:15px;border:.7px solid var(--soft-white);border-radius:50%;font-size:5px;color:var(--white);display:flex;align-items:center;justify-content:center}
  .light .copy{color:var(--ink-body)}
  .light .heading{color:var(--ink-dark)}
  .light .footer-rule{border-color:#9aa6ad}
  .light .folio{border-color:#6f6f6f;color:#333}
</style>
</head>
<body>
<div class="sheet-frame"></div>

<!-- Cover -->
<section class="page cover" style="left:151px;top:77px">
  <div class="photo" style="bottom:0;background:linear-gradient(180deg,#4b4e52 0%,#3a3c3e 30%,#222423 55%,#2f312e 75%,#4a4c49 100%)" role="img" aria-label="Dusk photograph of a dark timber-clad modular home with a garage and garden planting"></div>
  <h1 style="position:absolute;left:14px;top:12px;font-family:'Jost',sans-serif;font-weight:400;font-size:64px;letter-spacing:-2px;color:var(--white);line-height:1">Kestrel</h1>
  <div style="position:absolute;left:17px;right:17px;top:345px;border-top:.6px solid #9a9a9a"></div>
  <div style="position:absolute;left:17px;top:356px" class="wordmark">Kestrel</div>
  <div style="position:absolute;right:18px;top:353px;font-size:6.4px;line-height:1.25;color:var(--white);font-weight:300">PROPERTY INVESTMENT<br>PROPOSAL</div>
</section>

<!-- Business Overview -->
<section class="page light" style="left:455px;top:77px;background:#dfe9ef">
  <div class="photo" style="bottom:0;background:linear-gradient(180deg,#7fbde6 0%,#bcdcee 30%,#eef3f5 60%,#e8edef 66%,#3c3d3e 68%,#2a2b2c 80%,#9b9994 86%,#8e8c86 93%,#6f7f4e 100%)" role="img" aria-label="Modular home with an ocean-view glazed living room under a clear blue sky"></div>
  <h2 class="heading" style="top:44px"><span class="small">Business</span><span class="large">Overview</span></h2>
  <div class="copy" style="left:21px;top:92px;width:108px">
    <p>Kestrel Dwellings Developments, is an emerging New Zealand property investment company with a focus on providing unique property investment opportunities.</p>
    <p>Our expertise and capabilities in architectural modular homes provide us with a remarkable advantage in tackling the development of properties that are typically considered challenging, remote, or uniquely positioned.</p>
    <p>As a company, with 48 employees boasting a wealth of experience in handling complex architectural projects, making us well-equipped to navigate the intricacies and demands of such ventures.</p>
    <p>This advantage allows us to not only execute projects efficiently but also to deliver exceptional results within condensed time frames.</p>
  </div>
  <div class="copy" style="left:135px;top:92px;width:114px">
    <p>By capitalizing on our ability to develop difficult, remote, or one-of-a-kind properties swiftly and effectively, Kestrel Dwellings Developments offers investors a rare chance to engage in projects that promise exceptional profitability in the New Zealand property market.</p>
    <p>Our specialization in this niche sector of property development not only sets us apart from competitors, but also paves the way for lucrative investment opportunities in the New Zealand property market.</p>
  </div>
  <div class="page-footer"><span class="wordmark">Kestrel</span><span class="footer-rule"></span><span class="folio" style="border-color:#ddd;color:#fff">1</span></div>
</section>

<!-- Business Origins -->
<section class="page" style="left:759px;top:77px">
  <div class="photo" style="height:262px;background:linear-gradient(180deg,#8b8f8a 0%,#a39c86 14%,#6f6a55 24%,#48502b 45%,#5d6a2f 70%,#3f4820 100%)" role="img" aria-label="Coastal hilltop home on green pasture overlooking the sea at sunset"></div>
  <div class="panel" style="top:259px"></div>
  <h2 class="heading" style="top:164px"><span class="small">Business</span><span class="large">Origins</span></h2>
  <div class="copy" style="left:17px;top:218px;width:120px">
    <p>Kestrel Dwellings Developments was established with the goal of transforming the property investment market in New Zealand by introducing an innovative approach that centers on architectural modular designs and streamlined project timelines.</p>
    <p>Driven by our enthusiasm for architecture and real estate, we have expanded our successful business model to not only offer financial opportunities for investors but also to expand on our passion for high-end architectural design.</p>
    <p>With a wealth of experience accumulated over the past <u>six years</u> in the construction and the property market, we are pivoting to focus solely on our property development initiatives, presenting completed Kestrel projects to the market, in exclusive locations.</p>
  </div>
  <div class="copy" style="left:142px;top:218px;width:120px">
    <p>These projects will boast high-quality standards, meticulous attention to detail and landscaping, and creative design elements.</p>
    <p>By introducing completed Kestrel properties into the market, we aim to reach a wider audience, catering to individuals who prefer ready-to-occupy homes, over engaging in the design and construction process.</p>
    <p>This approach also simplifies the financing process for prospective buyers, as established properties are often preferred by financial lenders.</p>
  </div>
  <div class="page-footer"><span class="wordmark">Kestrel</span><span class="footer-rule"></span><span class="folio">2</span></div>
</section>

<!-- Competitive Advantage -->
<section class="page" style="left:152px;top:491px;height:385px;width:272px">
  <div class="photo" style="height:214px;background:linear-gradient(180deg,#6f7c63 0%,#3f4a33 30%,#262826 55%,#3b4136 80%,#a7aaa4 100%)" role="img" aria-label="Two-storey black modular home with a cantilevered upper level among lush trees"></div>
  <div class="panel" style="top:213px"></div>
  <h2 class="heading" style="top:163px;left:17px"><span class="small">Competitive</span><span class="large">Advantage</span></h2>
  <div class="copy" style="left:17px;top:224px;width:106px">
    <p>Our competitive advantage lies in the uniqueness of our property investment opportunities.</p>
    <p>Unlike traditional real estate companies, we focus on offering properties that are not only profitable but also <u>aesthetically pleasing and unique</u>.</p>
    <p>By catering to the tastes of architecture lovers, we set ourselves apart from the competition and attract a niche market of customers who appreciate the artistry and design of our projects.</p>
  </div>
  <div class="copy" style="left:128px;top:222px;width:112px">
    <p>Additionally, the streamlined and condensed timelines facilitated by our modular approach provide quicker returns on investment.</p>
  </div>
  <div class="page-footer"><span class="wordmark">Kestrel</span><span class="footer-rule"></span><span class="folio">3</span></div>
</section>

<!-- Financial Summary -->
<section class="page" style="left:455px;top:492px;height:384px;width:272px">
  <div class="photo" style="height:245px;background:linear-gradient(180deg,#b9bfc4 0%,#d2d1c8 30%,#6c6a5a 50%,#2e2f2c 62%,#5e6152 75%,#4b5a2c 100%)" role="img" aria-label="Single-level modular home with pool and lit garden lawn at dusk"></div>
  <div class="panel" style="top:243px"></div>
  <h2 class="heading" style="top:162px;left:16px"><span class="small">Financial</span><span class="large">Summary</span></h2>
  <div class="copy" style="left:18px;top:210px;width:100px;line-height:1.4">In terms of financial projections, with each development, we anticipate a profit of</div>
  <div style="position:absolute;left:18px;top:222px;font-size:10px;color:var(--white);font-weight:300">10%-20%</div>
  <div class="copy" style="left:18px;top:235px">which will be project dependent.</div>
  <div class="copy" style="left:17px;top:254px;width:108px">
    <p>This growth is fueled by the increasing demand for unique property investments in New Zealand and our ability to deliver high-quality services to the market in a condensed time frame, with heavily controlled costs.</p>
    <p>With a solid business model and a dedicated team, we are confident in our ability to achieve success and establish Kestrel Homes Investments as a trusted name in the industry.</p>
    <p>New Zealand's property market has been experiencing steady growth over the years,</p>
  </div>
  <div class="copy" style="left:128px;top:254px;width:112px">
    <p>making it an attractive destination for property investors. With its beautiful landscapes and strong economy, New Zealand offers a diverse range of investment opportunities for both local and international investors.</p>
    <p>The demand for quality properties in prime locations continues to rise, creating a favorable environment for property investment companies like ours that can lean on our modular benefits of being able to reach unique and remote locations.</p>
  </div>
  <div class="page-footer"><span class="wordmark">Kestrel</span><span class="footer-rule"></span><span class="folio">4</span></div>
</section>

<!-- Back cover -->
<section class="page" style="left:760px;top:489px;height:386px">
  <div class="photo" style="bottom:0;background:linear-gradient(180deg,#3d3f3f 0%,#353735 35%,#2a2c29 55%,#1f201e 70%,#2a2e25 85%,#3b4527 100%)" role="img" aria-label="Modular home with sunken outdoor terrace and palms in evening light"></div>
  <div style="position:absolute;left:16px;top:330px;font-family:'Jost',sans-serif;font-weight:400;font-size:22px;color:var(--white);letter-spacing:-.5px">Kestrel</div>
  <div style="position:absolute;right:17px;top:337px;display:flex;align-items:center;gap:4px">
    <span style="width:4px;height:4px;background:var(--white)"></span>
    <span style="font-size:6.2px;color:var(--white)">Kestrel Dwellings</span>
  </div>
  <div style="position:absolute;left:16px;right:16px;top:354px;border-top:.6px solid #9a9a9a"></div>
  <div style="position:absolute;left:16px;top:359px;font-size:4.6px;color:var(--white)">Email: sales@kestreldwellings.co.nz | Phone: 09 555 0142 | Visit us by appointment: Harbour Road, Auckland</div>
</section>
</body>
</html>
```